Marcus Delbridge Finance

Need a personal website Leasewell Equipment Finance,Business Finance,Commercial Finance, Construction Finance, Bridging Finance. Similar websites are www.corvalend.com.au / www.tarmivest.com.au / www.qbr7.com.au /wwwhalvecredit.com.au

Target Market(s)

Business People

Industry/Entity Type

Business

Number of Pages Required

3 page

Font styles to use
Serif
Sans Serif

Requirements
Must have
• All i want is a simple corporate looking website Leasewell Equipment Finance, Commercial Finance, Construction Finance, Business Finance, Bridging Finance,

```html
<!DOCTYPE html>
<html lang="en">
<head>
<meta charset="utf-8">
<title>Leasewell Equipment – Equipment Finance</title>
<link href="https://fonts.googleapis.com/css2?family=Roboto+Slab:wght@400;700&family=Open+Sans:wght@400;600;700&display=swap" rel="stylesheet">
<style>
:root{
  --blue:#29a8e0;
  --blue-dark:#1f8fc4;
  --green:#a5cd39;
  --ink:#2b2b2b;
  --muted:#666;
  --dark:#1c1c1c;
  --white:#fff;
  --panel:#f6f7f8;
}
*{box-sizing:border-box;margin:0;padding:0}
html,body{width:1200px;height:2837px;overflow:hidden}
body{font-family:"Open Sans",Arial,sans-serif;color:var(--ink);background:var(--white);position:relative}
.slab{font-family:"Roboto Slab",Georgia,serif}
section,header,footer{position:absolute;left:0;width:1200px}

/* header */
.site-header{top:0;height:123px;background:var(--white)}
.topbar{position:absolute;right:0;top:0;width:554px;height:42px;background:var(--blue);clip-path:polygon(30px 0,100% 0,100% 100%,0 100%)}
.topbar .mail{position:absolute;left:60px;top:11px;color:var(--white);font-size:14px;display:flex;align-items:center;gap:8px}
.social{display:flex;gap:10px}
.social span{width:26px;height:26px;border-radius:50%;background:var(--white);border:2px solid var(--blue-dark)}
.topbar .social{position:absolute;left:300px;top:7px}
.brand{position:absolute;left:133px;top:44px;display:flex;align-items:center;gap:10px}
.brand .mark{width:22px;height:22px;background:var(--green)}
.brand .name{font-family:"Roboto Slab",Georgia,serif;font-weight:700;font-size:19px;color:var(--ink)}
.main-nav{position:absolute;left:450px;top:82px;display:flex;gap:34px;font-size:13px}
.main-nav a{color:var(--ink);text-decoration:none}
.main-nav a.active{color:var(--blue);border-bottom:2px solid var(--blue);padding-bottom:4px}

/* hero */
.hero{top:123px;height:735px;background:var(--blue);overflow:hidden}
.hero-photo{position:absolute;left:0;top:0;width:1200px;height:523px;background:linear-gradient(120deg,#8a8f96,#cfd3d8 45%,#6d7178)}
.hero-curve{position:absolute;left:0;top:300px}
.hero-copy{position:absolute;left:0;width:1200px;top:120px;text-align:center;color:var(--white)}
.hero-copy h1{font-family:"Roboto Slab",Georgia,serif;font-weight:400;font-size:30px;line-height:36px}
.hero-copy p{font-size:15px;margin-top:22px;line-height:20px}
.btn{display:inline-flex;align-items:center;justify-content:center;font-size:14px;font-weight:600;text-decoration:none}
.btn-blue{background:var(--blue);color:var(--white)}
.hero-copy .btn{margin-top:28px;width:230px;height:43px;font-size:17px;font-weight:400;gap:8px}
.callback{position:absolute;top:550px;left:0;width:1200px;text-align:center;color:var(--white)}
.callback h2{font-family:"Roboto Slab",Georgia,serif;font-weight:400;font-size:25px}
.callback .fields{display:flex;justify-content:center;gap:12px;margin-top:24px}
.callback .field{width:283px;height:35px;background:var(--white);border-radius:2px;color:#aaa;font-size:9px;text-align:left;padding:11px 10px}
.callback .actions{display:flex;justify-content:center;gap:14px;margin-top:21px}
.callback .actions .btn{width:212px;height:43px;border:2px solid var(--white)}
.btn-white{background:var(--white);color:var(--blue)}
.btn-outline{color:var(--white)}

/* services */
.services{top:864px;height:390px;background:linear-gradient(180deg,#eef1f4,#f7f8fa 60%,#eef1f4)}
.section-title{font-family:"Roboto Slab",Georgia,serif;font-weight:400;font-size:25px;text-align:center}
.services .section-title{margin-top:38px}
.service-list{position:absolute;top:120px;left:0;width:1200px}
.service{position:absolute;width:220px;text-align:center}
.service .icon{width:80px;height:80px;margin:0 auto;border:3px solid var(--blue);border-radius:50%;display:flex;align-items:center;justify-content:center}
.service h3{font-family:"Roboto Slab",Georgia,serif;font-weight:400;font-size:16px;color:var(--blue);margin-top:22px}
.service p{font-size:11px;line-height:16px;color:#333;margin-top:8px}
.divider{display:flex;align-items:center;justify-content:center;margin-top:14px;gap:6px}
.divider i{display:block;width:60px;height:1px;background:var(--blue)}
.divider b{width:14px;height:14px;background:var(--green);color:var(--white);font-size:12px;line-height:14px}

/* testimonials */
.testimonials{top:1254px;height:374px;background:linear-gradient(135deg,#2a2a2a,#151515 60%,#2d2d2d);color:var(--white);text-align:center}
.testimonials .section-title{margin-top:38px;color:var(--white)}
.avatar{position:absolute;left:543px;top:104px;width:114px;height:114px;border-radius:50%;border:4px solid var(--white);background:linear-gradient(180deg,#c9ccd0,#8e949b)}
.testimonials .who{position:absolute;top:228px;width:1200px}
.testimonials .who strong{display:block;color:var(--blue);font-size:12px;font-weight:600}
.testimonials .who span{font-size:9px}
.testimonials blockquote{position:absolute;top:274px;left:225px;width:750px;font-size:11px;line-height:16px}
.arrow{position:absolute;top:208px;width:26px;height:26px;border-radius:50%}
.arrow-prev{left:129px;background:#d6d6d6}
.arrow-next{left:1037px;background:var(--green)}

/* finance panels */
.finance{top:1643px;height:340px}
.panel{position:absolute;background:var(--panel);box-shadow:0 1px 3px rgba(0,0,0,.08)}
.lease{left:133px;top:0;width:475px;height:332px;padding:26px 13px}
.lease h3{font-family:"Roboto Slab",Georgia,serif;font-weight:400;font-size:19px;color:var(--blue)}
.lease p{font-size:12px;line-height:18px;color:#555;margin-top:14px}
.panel .buttons{display:flex;gap:12px;margin-top:18px}
.panel .btn{height:41px;padding:0 22px}
.btn-line{border:2px solid var(--blue);color:var(--blue);background:var(--white)}
.tabs-panel{left:629px;top:38px;width:438px;height:294px;background:var(--white)}
.tabs{display:flex;height:50px;border:1px solid var(--blue)}
.tabs div{font-family:"Roboto Slab",Georgia,serif;font-size:15px;color:var(--blue);padding:0 16px;display:flex;align-items:center;border-right:1px solid var(--blue)}
.tabs div.active{background:var(--blue);color:var(--white)}
.tabs div:last-child{border-right:0}
.tab-body{padding:22px 12px;font-size:12px;line-height:18px;color:#555}
.tab-body .links{color:var(--blue);font-size:11px;margin-top:8px}

/* needs band */
.needs{top:2010px;height:298px;background:var(--blue);color:var(--white)}
.needs-photo{position:absolute;left:0;top:0;width:360px;height:298px;border-radius:0 0 180px 0;border-right:5px solid var(--green);border-bottom:5px solid var(--green);background:linear-gradient(160deg,#eef0f2,#aeb4ba 60%,#6f7780)}
.needs-copy{position:absolute;left:370px;top:22px;width:690px}
.needs-copy h2{font-family:"Roboto Slab",Georgia,serif;font-weight:400;font-size:23px}
.needs-copy p{font-size:12px;line-height:17px;margin-top:16px}
.needs-copy ul{list-style:none;margin-top:14px;font-size:12px;line-height:20px}
.needs-copy li::before{content:"›";color:var(--green);font-weight:700;font-size:17px;margin-right:8px}

/* blog */
.blog{top:2308px;height:300px}
.blog .section-title{margin-top:34px;color:var(--blue)}
.post{position:absolute;top:105px;width:350px}
.post .date{position:absolute;left:0;top:0;width:114px;height:114px;border-radius:50%;background:var(--blue);border:3px solid var(--green);color:var(--white);text-align:center;font-family:"Roboto Slab",Georgia,serif}
.post .date b{display:block;font-weight:400;font-size:36px;margin-top:18px;line-height:40px}
.post .date span{font-size:24px}
.post h3{position:absolute;left:131px;top:4px;width:300px;font-size:14px;font-weight:700}
.post p{position:absolute;left:131px;top:28px;width:300px;font-size:11px;line-height:16px;color:#555}

/* footer */
.site-footer{top:2560px;height:277px}
.footer-shape{position:absolute;left:0;top:0}
.footer-brand{position:absolute;left:380px;top:100px;width:230px;text-align:center;font-family:"Roboto Slab",Georgia,serif;font-weight:700;font-size:15px;color:var(--white)}
.footer-brand .mark{display:block;width:26px;height:26px;background:var(--white);margin:0 auto 10px}
.footer-rule{position:absolute;left:600px;top:52px;width:1px;height:110px;background:rgba(255,255,255,.5)}
.site-footer .social{position:absolute;left:630px;top:72px}
.site-footer .social span{width:32px;height:32px;border:0}
.site-footer .mail{position:absolute;left:630px;top:120px;color:var(--white);font-size:14px}
.footer-nav{position:absolute;top:198px;width:1200px;display:flex;justify-content:center;gap:34px;font-size:12px}
.footer-nav a{color:var(--white);text-decoration:none}
.footer-nav a.active{color:var(--dark)}
.copyright{position:absolute;top:240px;width:1200px;height:37px;background:var(--blue-dark);color:var(--white);font-size:11px;text-align:center;line-height:37px}
</style>
</head>
<body>

<header class="site-header">
  <div class="topbar">
    <div class="mail">
      <svg width="14" height="10" viewBox="0 0 14 10"><rect width="14" height="10" fill="#a5cd39"/><path d="M0 0l7 6 7-6" stroke="#fff" fill="none"/></svg>
      info@leasewell-equipment.com
    </div>
    <div class="social"><span></span><span></span><span></span><span></span></div>
  </div>
  <div class="brand"><span class="mark"></span><span class="name">Leasewell Equipment</span></div>
  <nav class="main-nav">
    <a class="active" href="#">Home</a><a href="#">Equipment Finance</a><a href="#">Business Finance</a><a href="#">Supplier Finance</a><a href="#">Equip Blog</a><a href="#">Contact Us</a>
  </nav>
</header>

<section class="hero">
  <div class="hero-photo" role="img" aria-label="Business people shaking hands in a bright office"></div>
  <svg class="hero-curve" width="1200" height="240" viewBox="0 0 1200 240">
    <path d="M0 70 C250 220 700 240 1200 120 L1200 240 L0 240Z" fill="#29a8e0"/>
    <path d="M0 110 C180 210 420 240 640 240" stroke="#a5cd39" stroke-width="10" fill="none"/>
  </svg>
  <div class="hero-copy">
    <h1>Easy Equipment Finance!<br>Fast Approvals to $50,000*</h1>
    <p>Equipment Finance,Business Finance,Commercial Finance,<br>Construction Finance, Bridging Finance</p>
    <a class="btn btn-blue" href="#">Contact Us
      <svg width="16" height="12" viewBox="0 0 16 12"><rect width="16" height="12" fill="#fff"/><path d="M0 0l8 7 8-7" stroke="#29a8e0" fill="none" stroke-width="1.5"/></svg>
    </a>
  </div>
  <div class="callback">
    <h2>Get Funded Today, enter details below for a call back</h2>
    <div class="fields"><div class="field">Phone Number</div><div class="field">Email</div></div>
    <div class="actions"><a class="btn btn-white" href="#">Get A Call Back</a><a class="btn btn-outline" href="#">Apply online</a></div>
  </div>
</section>

<section class="services">
  <h2 class="section-title">Our Services</h2>
  <div class="service-list">
    <div class="service" style="left:112px">
      <div class="icon"><svg width="40" height="40" viewBox="0 0 40 40"><circle cx="20" cy="20" r="15" fill="#29a8e0"/><text x="20" y="27" text-anchor="middle" font-size="20" font-weight="700" fill="#fff" font-family="Open Sans,sans-serif">$</text></svg></div>
      <h3>Equipment Finance</h3>
      <p>Lorem Ipsum is simply dummy text of the printing and typesetting industry. Lorem Ipsum has been the industry's</p>
      <div class="divider"><i></i><b>+</b><i></i></div>
    </div>
    <div class="service" style="left:355px">
      <div class="icon"><svg width="40" height="40" viewBox="0 0 40 40"><rect x="6" y="8" width="28" height="24" fill="none" stroke="#29a8e0" stroke-width="2"/><rect x="11" y="20" width="4" height="9" fill="#29a8e0"/><rect x="18" y="14" width="4" height="15" fill="#29a8e0"/><rect x="25" y="17" width="4" height="12" fill="#29a8e0"/></svg></div>
      <h3>Business Finance</h3>
      <p>Lorem Ipsum is simply dummy text of the printing and typesetting industry. Lorem Ipsum has been the industry's</p>
      <div class="divider"><i></i><b>+</b><i></i></div>
    </div>
    <div class="service" style="left:602px">
      <div class="icon"><svg width="40" height="40" viewBox="0 0 40 40"><circle cx="22" cy="14" r="7" fill="#29a8e0"/><path d="M5 28 h10 l8 3 h10 v4 H5z" fill="#29a8e0"/></svg></div>
      <h3>Commercial Finance</h3>
      <p>Lorem Ipsum is simply dummy text of the printing and typesetting industry. Lorem Ipsum has been the industry's</p>
      <div class="divider"><i></i><b>+</b><i></i></div>
    </div>
    <div class="service" style="left:845px">
      <div class="icon"><svg width="40" height="40" viewBox="0 0 40 40"><path d="M6 20 L20 8 L34 20 V33 H6Z" fill="#29a8e0"/><rect x="16" y="23" width="8" height="10" fill="#fff"/></svg></div>
      <h3>Compassionate</h3>
      <p>Lorem Ipsum is simply dummy text of the printing and typesetting industry. Lorem Ipsum has been the industry's</p>
      <div class="divider"><i></i><b>+</b><i></i></div>
    </div>
  </div>
</section>

<section class="testimonials" role="img" aria-label="Dark background of a business handshake">
  <h2 class="section-title">Testimonials</h2>
  <svg class="arrow arrow-prev" viewBox="0 0 26 26"><circle cx="13" cy="13" r="13" fill="#d6d6d6"/><path d="M15 7l-6 6 6 6" stroke="#222" stroke-width="3" fill="none"/></svg>
  <div class="avatar" role="img" aria-label="Portrait of the client giving the testimonial"></div>
  <svg class="arrow arrow-next" viewBox="0 0 26 26"><circle cx="13" cy="13" r="13" fill="#a5cd39"/><path d="M11 7l6 6-6 6" stroke="#222" stroke-width="3" fill="none"/></svg>
  <div class="who"><strong>Daniel Rourke</strong><span>Lorem Ipsum is simply dummy</span></div>
  <blockquote>Lorem Ipsum is simply dummy text of the printing and typesetting industry. Lorem Ipsum has been the industry's standard dummy text ever since the 1500s, when an unknown printer took a galley of type and scrambled it to make a type specimen book. It has survived not only five centuries, but also the leap into electronic typesetting, Lorem Ipsum is simply dummy text of the printing printer took a</blockquote>
</section>

<section class="finance">
  <div class="panel lease">
    <h3>Equipment Finance : Operating Lease</h3>
    <p>Being able to keep up with the latest equipment models, not having the hassle of disposing of obsolete gear, using up precious working capital and claiming payments as tax deductions are just a few of the benefits of choosing to use a finance option when next making a purchase. We are also specialists in all types of equipment lease options and will provide you with a range of choices each and every time.<br>Make the right decision today..</p>
    <div class="buttons"><a class="btn btn-blue" href="#">Speak with a specialist</a><a class="btn btn-line" href="#">I am a supplier, learn more</a></div>
  </div>
  <div class="panel tabs-panel">
    <div class="tabs"><div class="active">Invoice Factoring</div><div>Trade Finance</div><div>Business Loans</div></div>
    <div class="tab-body">
      <p>Access 85% of your existing and new invoice value within 24 hours. Waiting to be paid leaves you without cash in the bank and distracts from your focus to take on new opportunities. Pay bills and wages on time with funding that grows with your turnover and not your credit rating.</p>
      <p class="links">[Learn more] [Skip &amp; Apply for a quote]</p>
      <div class="buttons"><a class="btn btn-blue" href="#">Speak with a specialist</a></div>
    </div>
  </div>
</section>

<section class="needs">
  <div class="needs-photo" role="img" aria-label="Finance specialist in a grey suit"></div>
  <div class="needs-copy">
    <h2>We look after all of your finance needs</h2>
    <p>Take a minute to use our quick quote tool for a guide on your borrowing capacity, to compare loan rates and much more. Leave your details and one of our experienced team will call to discuss your situation at a time that suits you.</p>
    <ul><li>Equipment Finance</li><li>Business Finance</li><li>Commercial Finance</li><li>Construction Finance</li><li>Bridging Finance</li></ul>
    <p>Award winning brokers, individually tailored loans and professional service from our experienced team. Contact Corvalend today for all of your finance needs.</p>
  </div>
</section>

<section class="blog">
  <h2 class="section-title">Our Blog</h2>
  <article class="post" style="left:133px">
    <div class="date"><b>18</b><span>Dec</span></div>
    <h3>Lorem Ipsum is simply dummy text of the</h3>
    <p>Lorem Ipsum is simply dummy text of the printing and typesetting industry. Lorem Ipsum has been the industry's standard dummy text ever since the 1500s, when an unknown printer took a galley of type and scrambled it to make a type</p>
  </article>
  <article class="post" style="left:621px">
    <div class="date"><b>19</b><span>Dec</span></div>
    <h3>Lorem Ipsum is simply dummy text of the</h3>
    <p>Lorem Ipsum is simply dummy text of the printing and typesetting industry. Lorem Ipsum has been the industry's standard dummy text ever since the 1500s, when an unknown printer took a galley of type and scrambled it to make a type</p>
  </article>
</section>

<footer class="site-footer">
  <svg class="footer-shape" width="1200" height="277" viewBox="0 0 1200 277">
    <path d="M0 80 C300 0 900 0 1200 60 L1200 277 L0 277Z" fill="#a5cd39"/>
    <path d="M0 90 C300 12 900 12 1200 70 L1200 277 L0 277Z" fill="#29a8e0"/>
  </svg>
  <div class="footer-brand"><span class="mark"></span>Leasewell Equipment</div>
  <div class="footer-rule"></div>
  <div class="social"><span></span><span></span><span></span><span></span></div>
  <div class="mail">info@leasewell-equipment.com</div>
  <nav class="footer-nav">
    <a class="active" href="#">Home</a><a href="#">Equipment Finance</a><a href="#">Business Finance</a><a href="#">Supplier Finance</a><a href="#">Equip Blog</a><a href="#">Contact Us</a>
  </nav>
  <div class="copyright">Copyright 2016</div>
</footer>

</body>
</html>
```